Aunt Roula's Bakery

I am about to create a luxury boutique that specializes in cake baking and cupcake
and ready for parties and special events and order delivery
the logo has already made

Boutique

Email:auntroulasbakery@mailbox-example.net
Instagram: aunt_roula_bakery
Twitter: xxxxxxx
WhatsApp: xxxxxxx

Requirements
Must have
• luxury design

```html
<!DOCTYPE html>
<html lang="en">
<head>
<meta charset="utf-8">
<title>Aunt Roula's Bakery – Business Card</title>
<link rel="stylesheet" href="https://fonts.googleapis.com/css2?family=Cinzel:wght@400&family=Open+Sans:wght@400&display=swap">
<style>
  :root {
    --stage: #000000;
    --card-light: #f3f3f3;
    --card-pink: #dd9aab;
    --ink-grey: #6a6a6a;
    --accent-pink: #dd9aab;
    --ink-white: #ffffff;
  }
  * { margin: 0; padding: 0; box-sizing: border-box; }
  html, body {
    width: 1200px; height: 900px; overflow: hidden;
    background: var(--stage);
  }
  .canvas { position: relative; width: 1200px; height: 900px; }

  .card {
    position: absolute; top: 200px;
    width: 310px; height: 502px;
  }
  .card--contact {
    left: 293px;
    background: var(--card-light);
    border-radius: 58px 0 70px 0;
  }
  .card--brand {
    left: 613px;
    background: var(--card-pink);
    border-radius: 0 58px 0 70px;
  }

  .brand-mark {
    position: absolute; left: 0; right: 0;
    display: flex; flex-direction: column; align-items: center;
    font-family: "Cinzel", serif; font-weight: 400;
  }
  .card--contact .brand-mark { top: 15px; color: var(--ink-grey); }
  .card--brand .brand-mark { top: 142px; color: var(--ink-white); }

  .brand-mark__dot { border-radius: 50%; }
  .card--contact .brand-mark__dot {
    width: 60px; height: 60px; margin-bottom: 10px;
    background: var(--accent-pink);
  }
  .card--brand .brand-mark__dot {
    width: 70px; height: 70px; margin-bottom: 12px;
    background: var(--ink-white);
  }

  .brand-mark__name,
  .brand-mark__trade { white-space: nowrap; }
  .brand-mark__trade { letter-spacing: 0.32em; margin-left: 0.32em; }

  .card--contact .brand-mark__name { font-size: 30px; line-height: 1.1; }
  .card--contact .brand-mark__trade { font-size: 24px; line-height: 1.2; margin-top: 2px; }

  .card--brand .brand-mark__name { font-size: 35px; line-height: 1.1; }
  .card--brand .brand-mark__trade { font-size: 27px; line-height: 1.2; margin-top: 8px; }

  .contact-list {
    position: absolute; left: 24px; top: 392px;
    list-style: none;
    font-family: "Open Sans", sans-serif; font-size: 13px;
    color: var(--ink-grey);
  }
  .contact-list li {
    display: flex; align-items: center;
    height: 18px;
  }
  .contact-list__icon {
    width: 10px; height: 10px; margin-right: 13px; flex: none;
  }
  .contact-list__dot {
    width: 8px; height: 8px; margin: 0 14px 0 1px; flex: none;
    border-radius: 2px; background: var(--accent-pink);
  }
</style>
</head>
<body>
<main class="canvas">

  <section class="card card--contact" aria-label="Business card, contact side">
    <div class="brand-mark">
      <span class="brand-mark__dot"></span>
      <span class="brand-mark__name">AUNT ROULA'S</span>
      <span class="brand-mark__trade">BAKERY</span>
    </div>

    <ul class="contact-list">
      <li>
        <svg class="contact-list__icon" viewBox="0 0 10 8" aria-hidden="true">
          <rect x="0" y="0" width="10" height="8" rx="1" fill="#dd9aab"/>
          <path d="M0.6 1 L5 4.6 L9.4 1" fill="none" stroke="#f3f3f3" stroke-width="1"/>
        </svg>
        auntroulasbakery@mailbox-example.net
      </li>
      <li><span class="contact-list__dot"></span>aunt_roula_bakery</li>
      <li><span class="contact-list__dot"></span>XXXXXXX</li>
      <li><span class="contact-list__dot"></span>XXXXXXX</li>
    </ul>
  </section>

  <section class="card card--brand" aria-label="Business card, brand side">
    <div class="brand-mark">
      <span class="brand-mark__dot"></span>
      <span class="brand-mark__name">AUNT ROULA'S</span>
      <span class="brand-mark__trade">BAKERY</span>
    </div>
  </section>

</main>
</body>
</html>
```